Business Card Design - ChoiceCraft

Looking for creative, modern design, two sided for ChoiceCraft that is consistent with color and feel of website www.choicecraftpro.net.
Updates

Back of card will be used to promote products or have a quote revolving around decisions, change, leadership, innovation, creativity. Back should also have space to promote website, but optional to use the icon. Front of the card will need to use the icon and have standard place for name, job title, phone and email. We are not looking to put a mailing address or fax. Also want space to place a few words/phrase explaining what we do...such as individual growth and organizational development or tools, training, information...in addition, want the facebook icon small on the front somewhere as we are also on facebook.

Vector file uploaded of icon.

Target Market(s)

Professional coaching for individual growth and organizational development

Industry/Entity Type

Business

Requirements
Must have
• Icon...see attached.

```html
<!DOCTYPE html>
<html lang="en">
<head>
<meta charset="utf-8">
<title>ChoiceCraft Business Card</title>
<link href="https://fonts.googleapis.com/css2?family=Arimo:wght@400;700&family=Tinos:wght@400;700&display=swap" rel="stylesheet">
<style>
  :root {
    --stage: #d9dbde;
    --card: #ffffff;
    --card-edge: #9a9da2;
    --blue-deep: #0a63b0;
    --blue-mid: #1d86d0;
    --blue-light: #49b6ee;
    --accent: #2a9ad8;
    --swoosh-grey: #8c8f96;
    --ink: #1e1e1e;
    --ink-soft: #333333;
    --rule: #bfc3c8;
    --mark-fill: #c9dcee;
    --mark-ring: #5aa9e0;
  }
  * { margin: 0; padding: 0; box-sizing: border-box; }
  html, body { width: 1200px; height: 392px; overflow: hidden; background: var(--stage); }
  .canvas { position: relative; width: 1200px; height: 392px; }

  .card {
    position: absolute; top: 39px; width: 538px; height: 304px;
    background: var(--card); border-radius: 18px; overflow: hidden;
    box-shadow: 0 0 0 1px var(--card-edge);
  }
  .card--front { left: 51px; }
  .card--back { left: 610px; width: 533px; }

  .front-band { position: absolute; left: 0; top: 0; width: 538px; height: 170px; }
  .holder { position: absolute; right: 30px; top: 14px; text-align: right; color: #fff; font-family: "Arimo", Arial, sans-serif; }
  .holder__name { font-size: 21px; font-weight: 700; line-height: 1.2; }
  .holder__title { font-size: 15px; line-height: 1.2; }

  .brand-mark {
    position: absolute; left: 72px; top: 114px; width: 104px; height: 104px;
    border-radius: 50%; background: radial-gradient(circle at 40% 35%, #e6eef7, var(--mark-fill));
    border: 6px solid var(--mark-ring);
  }
  .brand-name {
    position: absolute; left: 30px; top: 242px; width: 210px; text-align: center;
    font-family: "Tinos", "Times New Roman", serif; font-weight: 700; font-size: 21px; color: var(--ink);
  }
  .divider { position: absolute; left: 258px; top: 136px; width: 1px; height: 134px; background: var(--rule); }

  .contact { position: absolute; left: 278px; top: 145px; list-style: none;
    font-family: "Tinos", "Times New Roman", serif; font-size: 13.5px; color: var(--ink-soft); line-height: 19px; }
  .contact li { display: flex; align-items: center; gap: 6px; }
  .contact svg { width: 10px; height: 10px; flex: none; }
  .social-square { width: 9px; height: 9px; background: #3b5a9a; border-radius: 1px; flex: none; }
  .tagline { position: absolute; left: 278px; top: 230px;
    font-family: "Tinos", "Times New Roman", serif; font-size: 13.5px; color: var(--ink-soft); line-height: 17px; }

  .quotes { position: absolute; left: 20px; top: 22px; list-style: none; font-family: "Arimo", Arial, sans-serif; }
  .quote { position: relative; padding-left: 38px; height: 53.5px; }
  .quote__dot { position: absolute; left: 2px; top: 5px; width: 18px; height: 18px; border-radius: 50%;
    background: var(--mark-fill); border: 2px solid var(--mark-ring); }
  .quote__text { font-size: 13.5px; color: var(--ink); line-height: 20px; }
  .quote__text::before { content: "\201C"; font-size: 24px; font-weight: 700; vertical-align: -6px; margin-right: 2px; position: absolute; left: 24px; top: 0; }
  .quote__text::after { content: "\201D"; font-size: 24px; font-weight: 700; vertical-align: -12px; margin-left: 2px; }
  .quote__author { font-size: 13.5px; font-weight: 700; color: var(--accent); line-height: 16px; }
  .quote__author span { color: var(--ink); font-weight: 400; }

  .back-mark {
    position: absolute; left: 345px; top: 152px; width: 130px; height: 130px; border-radius: 50%;
    background: radial-gradient(circle at 40% 35%, #eef4fa, #d6e6f4); border: 7px solid #9ccbee;
    display: flex; align-items: center; justify-content: center;
  }
  .back-mark__name { font-family: "Arimo", Arial, sans-serif; font-weight: 700; font-size: 16px; color: var(--accent); }
</style>
</head>
<body>
<div class="canvas">

  <section class="card card--front">
    <svg class="front-band" viewBox="0 0 538 170" aria-hidden="true">
      <defs>
        <linearGradient id="bandBlue" x1="0" y1="0" x2="1" y2="0">
          <stop offset="0" stop-color="var(--blue-deep)"/>
          <stop offset="0.55" stop-color="var(--blue-mid)"/>
          <stop offset="1" stop-color="var(--blue-light)"/>
        </linearGradient>
        <linearGradient id="swooshGrey" x1="0" y1="0" x2="1" y2="0">
          <stop offset="0" stop-color="#3d4047"/>
          <stop offset="0.5" stop-color="var(--swoosh-grey)"/>
          <stop offset="1" stop-color="#d4d6da"/>
        </linearGradient>
      </defs>
      <path d="M0,0 H538 V152 C450,110 330,70 180,60 C110,56 50,62 0,72 Z" fill="url(#bandBlue)"/>
      <path d="M0,86 C70,60 190,54 300,70 C390,84 470,112 538,150 V158 C470,124 390,96 300,82 C190,66 80,70 0,92 Z" fill="url(#swooshGrey)"/>
      <path d="M0,72 C50,62 110,56 180,60 C110,62 50,70 0,82 Z" fill="#ffffff" opacity="0.6"/>
    </svg>
    <div class="holder">
      <p class="holder__name">Your Name</p>
      <p class="holder__title">Title</p>
    </div>

    <div class="brand-mark"></div>
    <p class="brand-name">ChoiceCraft</p>

    <div class="divider"></div>
    <ul class="contact">
      <li><svg viewBox="0 0 10 10"><path d="M2,1 L4,1 L4.6,3 L3.4,3.8 C4,5.2 4.8,6 6.2,6.6 L7,5.4 L9,6 L9,8 C5,8.6 1.4,5 2,1 Z" fill="#333"/></svg>123-456-789</li>
      <li><svg viewBox="0 0 10 10"><rect x="0.5" y="2" width="9" height="6.5" fill="#333"/><path d="M0.5,2 L5,5.5 L9.5,2" stroke="#fff" fill="none"/></svg>info@choicecraftpro.net</li>
      <li><svg viewBox="0 0 10 10"><circle cx="5" cy="5" r="4.3" fill="none" stroke="#333" stroke-width="1.2"/><path d="M0.7,5 H9.3 M5,0.7 C2.5,3 2.5,7 5,9.3 M5,0.7 C7.5,3 7.5,7 5,9.3" stroke="#333" fill="none" stroke-width="0.8"/></svg>www.choicecraftpro.net</li>
      <li><span class="social-square"></span>/choicecraftpro</li>
    </ul>
    <p class="tagline">Supporting individual growth<br>and organizational development.</p>
  </section>

  <section class="card card--back">
    <div class="back-mark"><span class="back-mark__name">ChoiceCraft</span></div>
    <ul class="quotes">
      <li class="quote"><span class="quote__dot"></span>
        <p class="quote__text">Try not to become a man of success, but rather a man of value.</p>
        <p class="quote__author"><span>- </span>Arden Wells</p></li>
      <li class="quote"><span class="quote__dot"></span>
        <p class="quote__text">The only constant is change.</p>
        <p class="quote__author"><span>- </span>Theron of Kos</p></li>
      <li class="quote"><span class="quote__dot"></span>
        <p class="quote__text">We are what we repeatedly do. Excellence is not an act, it is a habit.</p>
        <p class="quote__author"><span>- </span>Castor Lyrian</p></li>
      <li class="quote"><span class="quote__dot"></span>
        <p class="quote__text">Simplicity is the ultimate sophistication.</p>
        <p class="quote__author"><span>- </span>Marco Bellandi</p></li>
      <li class="quote"><span class="quote__dot"></span>
        <p class="quote__text">Life is not fair - get used to it.</p>
        <p class="quote__author"><span>- </span>Wes Hartley</p></li>
    </ul>
  </section>

</div>
</body>
</html>
```